SkyvornQ Business Cards and Stationary Design

Need a design for our business cards and stationary. I want to carry on the theme of the logo. I want the business cards to have a design on the back. I would like the business cards and the stationary to carry the same theme, design scheme, and branding

Target Market(s)

Airlines and Maintenance Facilities

Industry/Entity Type

Aviation

Contact Information for Business Card

Name
Position Title
Address: 4827 Trellis Hollow Road, Marlow Bend, Oregon, 97214
Office Number
Mobile Number
Email
Website

Font styles to use
Serif
Sans Serif

Colors

Designer to choose colors to be used in the design.

```html
<!DOCTYPE html>
<html lang="en">
<head>
<meta charset="utf-8">
<title>SkyvornQ Business Card</title>
<link href="https://fonts.googleapis.com/css2?family=Open+Sans:wght@400;700&display=swap" rel="stylesheet">
<style>
  :root {
    --navy: #0b2550;
    --navy-deep: #0a2a66;
    --sky: #1f8fd8;
    --white: #ffffff;
    --backdrop: #2b2b2d;
  }
  * { margin: 0; padding: 0; box-sizing: border-box; }
  html, body {
    width: 1200px; height: 900px; overflow: hidden;
    background: var(--backdrop);
    font-family: "Open Sans", Arial, sans-serif;
  }
  .canvas { position: relative; width: 1200px; height: 900px; }
  .card {
    position: absolute; width: 560px; height: 320px;
    border-radius: 18px; overflow: hidden;
  }
  .card-front { left: 170px; top: 100px; background: var(--white); }
  .card-back { left: 470px; top: 480px; background: var(--navy); }
  .wave { position: absolute; inset: 0; width: 100%; height: 100%; }

  .brand { position: absolute; display: flex; align-items: center; gap: 12px; }
  .brand-mark { border-radius: 50%; border: 5px solid; flex: none; }
  .brand-name { font-weight: 700; letter-spacing: 6px; white-space: nowrap; }

  .card-front .brand { left: 30px; top: 150px; }
  .card-front .brand-mark { width: 44px; height: 44px; border-color: var(--sky); }
  .card-front .brand-name { font-size: 28px; color: var(--navy); }

  .contact {
    position: absolute; right: 24px; top: 82px;
    text-align: right; color: var(--white);
  }
  .person-name { font-size: 15px; font-weight: 700; letter-spacing: .5px; line-height: 20px; }
  .person-title { font-size: 12px; margin-bottom: 16px; }
  .contact-line {
    display: flex; justify-content: flex-end; align-items: center;
    gap: 6px; font-size: 12.5px; line-height: 19px; white-space: nowrap;
  }
  .contact-line svg { width: 11px; height: 11px; fill: var(--white); }
  .address {
    position: absolute; right: 24px; bottom: 24px;
    color: var(--white); font-size: 12.5px; white-space: nowrap;
  }

  .card-back .brand { left: 50%; top: 112px; transform: translateX(-50%); }
  .card-back .brand-mark { width: 56px; height: 56px; border-color: var(--white); }
  .card-back .brand-name { font-size: 36px; color: var(--white); }
  .website {
    position: absolute; left: 0; right: 0; top: 226px;
    display: flex; justify-content: center; align-items: center; gap: 14px;
    color: var(--white); font-size: 13px;
  }
  .website .rule { width: 30px; height: 1px; background: var(--white); }
</style>
</head>
<body>
<main class="canvas">
  <section class="card card-front">
    <svg class="wave" viewBox="0 0 560 320" aria-hidden="true">
      <path d="M447 0 C372 40 362 192 252 247 C182 287 72 282 0 262" fill="none" stroke="var(--sky)" stroke-width="4"/>
      <path d="M458 0 C383 40 373 200 263 255 C193 295 83 290 0 270 L0 320 L560 320 L560 0 Z" fill="var(--navy)"/>
      <path d="M0 252 C70 282 150 292 235 276" fill="none" stroke="var(--navy-deep)" stroke-width="5"/>
    </svg>
    <div class="brand">
      <span class="brand-mark"></span>
      <span class="brand-name">SKYVORNQ</span>
    </div>
    <div class="contact">
      <div class="person-name">DORIAN VANCE</div>
      <div class="person-title">President</div>
      <div class="contact-line">001 555 0148
        <svg viewBox="0 0 24 24"><path d="M6.6 10.8a15 15 0 0 0 6.6 6.6l2.2-2.2c.3-.3.7-.4 1-.2 1.1.4 2.3.6 3.6.6.6 0 1 .4 1 1V20c0 .6-.4 1-1 1A17 17 0 0 1 3 4c0-.6.4-1 1-1h3.5c.6 0 1 .4 1 1 0 1.3.2 2.5.6 3.6.1.3 0 .7-.2 1z"/></svg></div>
      <div class="contact-line">001 555 0193
        <svg viewBox="0 0 24 24"><path d="M7 1h10a2 2 0 0 1 2 2v18a2 2 0 0 1-2 2H7a2 2 0 0 1-2-2V3a2 2 0 0 1 2-2zm0 3v14h10V4z"/></svg></div>
      <div class="contact-line">info@skyvornq.com
        <svg viewBox="0 0 24 24"><path d="M2 5h20v14H2zm2 2v.5l8 5 8-5V7z"/></svg></div>
      <div class="contact-line">www.skyvornq.com
        <svg viewBox="0 0 24 24"><path d="M12 2a10 10 0 1 0 0 20 10 10 0 0 0 0-20zm0 2c1 0 2.4 2.3 2.8 7H9.2C9.6 6.3 11 4 12 4zm-2.8 9h5.6c-.4 4.7-1.8 7-2.8 7s-2.4-2.3-2.8-7z"/></svg></div>
    </div>
    <div class="address">4827 Trellis Hollow Road, Marlow Bend, Oregon, 97214</div>
  </section>

  <section class="card card-back">
    <div class="brand">
      <span class="brand-mark"></span>
      <span class="brand-name">SKYVORNQ</span>
    </div>
    <div class="website">
      <span class="rule"></span>
      <span>www.skyvornq.com</span>
      <span class="rule"></span>
    </div>
  </section>
</main>
</body>
</html>
```